Shopify Web-Page "Tiny-ThreadDays

We are building a new business in Switzerland offering premium sewing holiday camps for kids aged 9–14. In enclosed brief outlines our requirements for a complete Shopify homepage design and a multilingual logo creation.
Domains: tiny-threaddays.ch ; tiny-giornifilo.ch ; tiny-fadentage.ch

Project Overview
We are looking for:
1. A modern, fully designed Shopify homepage in English using standard Shopify content blocks (no custom coding), which we can later update ourselves. Supporting Multilanguage (EN, German, Italian).

2. A logo design that includes the brand identity and communicates our multilingual, creative, and child-focused positioning.

All details in enclosed

```html
<!DOCTYPE html>
<html lang="en">
<head>
<meta charset="utf-8">
<title>Tiny-ThreadDays – Creative Holiday Sewing Camps</title>
<link rel="stylesheet" href="https://fonts.googleapis.com/css2?family=Poppins:wght@300;400;500;600&display=swap">
<style>
:root{
  --coral:#f0585a;
  --teal:#48a09c;
  --navy:#1c3557;
  --ink:#222;
  --muted:#555;
  --topbar:#dfe4f7;
  --white:#fff;
  --line:#ddd;
}
*{margin:0;padding:0;box-sizing:border-box}
html,body{width:1200px;height:4870px;overflow:hidden}
body{font-family:"Poppins",sans-serif;color:var(--ink);background:var(--white);position:relative}
.abs{position:absolute}
.topbar{left:0;top:0;width:1200px;height:40px;background:var(--topbar)}
.social-dot{position:absolute;top:14px;width:11px;height:11px;border-radius:50%;background:#333}
.lang{position:absolute;right:140px;top:9px;height:20px;padding:0 10px;background:#eef0fa;font-size:8px;line-height:20px;color:#333}
.header{left:0;top:40px;width:1200px;height:106px;background:var(--white)}
.brand{position:absolute;display:flex;align-items:center;gap:8px;font-weight:600;font-size:20px;line-height:1;white-space:nowrap}
.brand .dot{width:12px;height:12px;border-radius:50%;background:var(--teal)}
.brand-header{left:144px;top:44px;color:var(--coral)}
.brand-footer{left:144px;top:4600px;color:var(--white)}
.nav{position:absolute;left:425px;top:46px;display:flex;gap:30px;font-size:13px}
.search{position:absolute;left:1040px;top:49px}
.hero{left:0;top:146px;width:1200px;height:627px;background:linear-gradient(100deg,#7b3b2a 0%,#b56b3e 30%,#c28d6b 55%,#6b5a55 80%,#3d3b45 100%)}
.hero h1{position:absolute;left:142px;top:160px;width:480px;font-weight:400;font-size:40px;line-height:52px;color:var(--white)}
.hero p{position:absolute;left:142px;top:334px;font-size:15px;color:var(--white)}
.btn{display:inline-block;background:var(--coral);color:var(--white);font-size:13px;border-radius:5px;text-align:center}
.hero .btn{position:absolute;left:144px;top:383px;width:138px;height:42px;line-height:42px}
.photo{position:absolute}
h2{font-weight:400;font-size:38px;color:var(--ink)}
.about-text{left:692px;top:950px;width:370px}
.about-text p{font-size:12px;line-height:26px;margin-top:22px}
.about-text .btn{margin-top:30px;width:138px;height:44px;line-height:44px}
.steps{left:0;top:1472px;width:1200px;height:431px;background:var(--teal);color:var(--white)}
.steps h2{color:var(--white);text-align:center;margin-top:80px}
.step{position:absolute;top:168px;width:180px;text-align:center}
.step .num{width:62px;height:62px;border-radius:50%;background:var(--white);color:var(--ink);font-size:24px;line-height:62px;margin:0 auto}
.step h3{font-weight:400;font-size:14px;margin-top:22px}
.step p{font-size:12px;line-height:22px;margin-top:16px}
.center{text-align:center;width:1200px;left:0}
.camp-label{position:absolute;top:2336px;width:282px;text-align:center;font-size:19px}
.why-list{left:668px;top:2660px;list-style:none;font-size:12px}
.why-list li{height:34.5px;display:flex;align-items:center;gap:6px}
.contact{left:0;top:3111px;width:1200px;height:359px;background:var(--navy);color:var(--white);text-align:center}
.contact h2{color:var(--white);margin-top:90px}
.contact p{font-size:18px;margin-top:18px}
.contact .btn{margin-top:22px;width:138px;height:44px;line-height:44px}
.faq{left:274px;top:3635px;width:722px;list-style:none}
.faq li{height:56.5px;border-bottom:1px solid var(--line);display:flex;justify-content:space-between;align-items:center;padding:0 10px;font-size:15px}
.faq li span:last-child{font-size:24px;font-weight:300}
.footer{left:0;top:4364px;width:1200px;height:506px;background:var(--navy);color:var(--white)}
.newsletter{left:125px;top:4207px;width:950px;height:276px;background:var(--teal);color:var(--white);text-align:center}
.newsletter h2{color:var(--white);margin-top:60px}
.newsletter p{font-size:12px;margin-top:10px}
.email{position:absolute;left:227px;top:168px;width:498px;height:50px;background:var(--white);color:#555;font-size:12px;text-align:left;padding:0 16px;line-height:50px}
.email b{position:absolute;right:22px;font-weight:400;color:#333}
.fcol{position:absolute;top:4556px;font-size:16px;color:var(--white)}
.fcol h4{font-weight:500;font-size:16px;margin-bottom:16px}
.fcol li{list-style:none;height:34px}
.copy{left:140px;top:4680px;font-size:11px;color:var(--white)}
</style>
</head>
<body>

<div class="abs topbar">
  <span class="social-dot" style="left:148px"></span>
  <span class="social-dot" style="left:174px"></span>
  <span class="social-dot" style="left:200px"></span>
  <span class="social-dot" style="left:226px"></span>
  <span class="lang">ENGLISH ▾</span>
</div>

<header class="abs header">
  <div class="brand brand-header">Tiny-ThreadDays<span class="dot"></span></div>
  <nav class="nav"><span>Home</span><span>About Us</span><span>Camps</span><span>How It Works</span><span>FAQ</span><span>Contact</span></nav>
  <svg class="search" width="14" height="14" viewBox="0 0 14 14"><circle cx="6" cy="6" r="4.5" fill="none" stroke="#222" stroke-width="2"/><line x1="9.5" y1="9.5" x2="13" y2="13" stroke="#222" stroke-width="2"/></svg>
</header>

<section class="abs hero" role="img" aria-label="Girl smiling at a craft table with colourful fabrics behind her">
  <h1>Creative Holiday Sewing Camps for Kids (Ages 9–14)</h1>
  <p>Fun, fashion, and creativity – in English, German &amp; Italian.</p>
  <span class="btn">Explore Camps</span>
</section>

<div class="photo" style="left:145px;top:884px;width:424px;height:434px;background:linear-gradient(135deg,#8a6a4a,#c9a07a 60%,#6a5040)" role="img" aria-label="Teacher smiling with young children"></div>
<div class="photo" style="left:396px;top:1121px;width:210px;height:243px;background:linear-gradient(160deg,#a47a58,#e1c19a 60%,#7d6048);border:2px solid #fff" role="img" aria-label="Children working on a craft project together"></div>
<div class="abs about-text">
  <h2>About Us</h2>
  <p>With over 10 years of experience in teaching children sewing, design, and creativity, Lena and Marta bring fun, structure, and imagination together.</p>
  <p>In small groups of up to 8 children, each young talent experiences a creative week full of color, laughter, and achievement.</p>
  <span class="btn">Explore More</span>
</div>

<section class="abs steps">
  <h2>How the Camp Works</h2>
  <div class="step" style="left:20px"><div class="num">1</div><h3>Project Selection</h3><p>Your child chooses their model &amp; pattern</p></div>
  <div class="step" style="left:264px"><div class="num">2</div><h3>Fabric Selection</h3><p>Premium fabrics provided</p></div>
  <div class="step" style="left:510px"><div class="num">3</div><h3>Sewing Basics</h3><p>Learn to use a real sewing machine</p></div>
  <div class="step" style="left:754px"><div class="num">4</div><h3>Create &amp; Refine</h3><p>Step-by-step guidance</p></div>
  <div class="step" style="left:1000px"><div class="num">5</div><h3>Showtime!</h3><p>Fashion show or photoshoot at the end</p></div>
</section>

<h2 class="abs center" style="top:1998px;text-align:center">Upcoming Camps</h2>
<div class="photo" style="left:145px;top:2086px;width:282px;height:225px;background:linear-gradient(135deg,#6b4a35,#b08866 55%,#5a3e2e)" role="img" aria-label="Spools of thread and buttons on a table"></div>
<div class="photo" style="left:459px;top:2086px;width:282px;height:225px;background:linear-gradient(135deg,#b06a3a,#d89a5c 50%,#8a5a35)" role="img" aria-label="Hands holding a handmade fabric toy"></div>
<div class="photo" style="left:773px;top:2086px;width:282px;height:225px;background:linear-gradient(135deg,#e8ecef,#cfd8d8 50%,#9cc4b8)" role="img" aria-label="Girl sewing at a sewing machine"></div>
<span class="camp-label" style="left:145px">Spring Camps</span>
<span class="camp-label" style="left:459px">Summer Camps</span>
<span class="camp-label" style="left:773px">Autumn Camps</span>

<div class="photo" style="left:132px;top:2508px;width:436px;height:434px;background:linear-gradient(135deg,#d9c6c0,#b35a4e 55%,#7a3a3a)" role="img" aria-label="Mother and daughter sewing together"></div>
<div class="photo" style="left:384px;top:2742px;width:212px;height:246px;background:linear-gradient(160deg,#e6ddd2,#c8342e 55%,#3aa04a);border:2px solid #fff" role="img" aria-label="Child in red with yellow yarn"></div>
<h2 class="abs" style="left:660px;top:2585px">Why Parents Choose Us</h2>
<ul class="abs why-list">
  <li><svg width="11" height="11" viewBox="0 0 11 11"><rect x=".5" y=".5" width="10" height="10" fill="none" stroke="#222"/><path d="M2.5 5.5l2 2 4-4" fill="none" stroke="#222" stroke-width="1.3"/></svg>Small groups &amp; personalized attention</li>
  <li><svg width="11" height="11" viewBox="0 0 11 11"><rect x=".5" y=".5" width="10" height="10" fill="none" stroke="#222"/><path d="M2.5 5.5l2 2 4-4" fill="none" stroke="#222" stroke-width="1.3"/></svg>Multilingual supervision (DE / EN / IT)</li>
  <li><svg width="11" height="11" viewBox="0 0 11 11"><rect x=".5" y=".5" width="10" height="10" fill="none" stroke="#222"/><path d="M2.5 5.5l2 2 4-4" fill="none" stroke="#222" stroke-width="1.3"/></svg>High-quality fabrics &amp; top-quality sewing machines (Stitchwell)</li>
  <li><svg width="11" height="11" viewBox="0 0 11 11"><rect x=".5" y=".5" width="10" height="10" fill="none" stroke="#222"/><path d="M2.5 5.5l2 2 4-4" fill="none" stroke="#222" stroke-width="1.3"/></svg>Encouragement of creativity, self-confidence, and fine motor skills</li>
  <li><svg width="11" height="11" viewBox="0 0 11 11"><rect x=".5" y=".5" width="10" height="10" fill="none" stroke="#222"/><path d="M2.5 5.5l2 2 4-4" fill="none" stroke="#222" stroke-width="1.3"/></svg>Safe, loving environment in Zurich, various places easy to reach</li>
  <li><svg width="11" height="11" viewBox="0 0 11 11"><rect x=".5" y=".5" width="10" height="10" fill="none" stroke="#222"/><path d="M2.5 5.5l2 2 4-4" fill="none" stroke="#222" stroke-width="1.3"/></svg>Pick-up Service from the Main-Station</li>
</ul>

<section class="abs contact">
  <h2>Get in Touch With Us</h2>
  <p>Join the next Kids Sewing Camp today!</p>
  <span class="btn">Explore More</span>
</section>

<h2 class="abs center" style="top:3548px;text-align:center">Frequently Asked Questions</h2>
<ul class="abs faq">
  <li><span>Does my child need sewing experience?</span><span>+</span></li>
  <li><span>What is included in the price?</span><span>+</span></li>
  <li><span>How does the pick-up service work?</span><span>+</span></li>
  <li><span>How big are the groups?</span><span>+</span></li>
  <li><span>Are materials provided?</span><span>+</span></li>
  <li><span>Where are the camps held?</span><span>+</span></li>
  <li><span>What languages are spoken?</span><span>+</span></li>
  <li><span>How can I register?</span><span>+</span></li>
  <li style="border-bottom:none"><span>What should my child bring?</span><span>+</span></li>
</ul>

<footer class="abs footer"></footer>
<section class="abs newsletter">
  <h2>Stay in the Loop!</h2>
  <p>Get updates about new camps, early-bird offers &amp; creative tips</p>
  <div class="email">Enter Email Address<b>»</b></div>
</section>

<div class="brand brand-footer">Tiny-ThreadDays<span class="dot"></span></div>
<p class="abs copy">Copyright@2025.All Rights Reserved</p>
<div class="fcol" style="left:452px"><h4>Quick Links</h4><ul><li>Home</li><li>About</li><li>Camps</li><li>FAQ</li><li>Contact</li></ul></div>
<div class="fcol" style="left:667px"><h4>Contact Us</h4><ul><li>hello@tiny-threaddays.ch</li><li>+41 44 555 01 23</li></ul></div>
<div class="fcol" style="left:953px"><h4>Social media</h4><ul><li>Community</li><li>Gallery</li><li>Network</li></ul></div>

</body>
</html>
```